Business Card Design for company

We want new business cards. We'd like something different-- yet still highly professional. Our tagline is Providing leadership, delivering success. Stock photos are ok, as long as they are relevant and look upscale.

Target Market(s)

Architecture/Business Management Consulting/Engineering Consulting

Contact Information for Business Card

dark gray background with pops of blue might be good, but you tell me. You're the designers. Rounded corners might be nice, but again, you tell me.

Font styles to use
Serif
Sans Serif

Colors
3276b5
5c5c5c
9d9d9d
fbfbfb

Requirements
Nice to have
• Something different, but still very professional.

```html
<!DOCTYPE html>
<html lang="en">
<head>
<meta charset="utf-8">
<title>Veratus Global – Business Card</title>
<link href="https://fonts.googleapis.com/css2?family=Montserrat:wght@400;500;700&family=Arimo:wght@400&display=swap" rel="stylesheet">
<style>
  :root {
    --brand-blue: #2f77bd;
    --brand-blue-deep: #2a6db0;
    --map-dot: #4f93d3;
    --paper: #fbfbfb;
    --backdrop: #2b2b2b;
    --ink-white: #ffffff;
  }
  html, body {
    margin: 0;
    padding: 0;
    width: 1200px;
    height: 930px;
    overflow: hidden;
    background: var(--backdrop);
  }
  .canvas {
    position: relative;
    width: 1200px;
    height: 930px;
  }
  .card {
    position: absolute;
    width: 560px;
    height: 320px;
    border-radius: 18px;
    overflow: hidden;
    background: var(--brand-blue);
    box-shadow: 0 10px 26px rgba(0,0,0,0.45);
    font-family: "Montserrat", sans-serif;
    color: var(--ink-white);
  }
  .card--front { left: 70px; top: 110px; }
  .card--back  { left: 570px; top: 500px; }

  /* Front */
  .world-map {
    position: absolute;
    left: 30px; top: 22px;
    width: 500px; height: 250px;
  }
  .front-wordmark {
    position: absolute;
    left: 0; right: 0; top: 118px;
    text-align: center;
    font-weight: 500;
    font-size: 40px;
    letter-spacing: 3px;
    text-transform: uppercase;
  }
  .front-tagline {
    position: absolute;
    left: 0; right: 0; top: 182px;
    text-align: center;
    font-weight: 500;
    font-size: 11px;
    letter-spacing: 1.6px;
    text-transform: uppercase;
  }

  /* Back */
  .back-wordmark {
    position: absolute;
    left: 26px; top: 104px;
    width: 220px;
    font-weight: 500;
    font-size: 30px;
    line-height: 1.1;
    letter-spacing: 2px;
    text-transform: uppercase;
    text-align: center;
  }
  .back-divider {
    position: absolute;
    left: 268px; top: 54px;
    width: 1px; height: 150px;
    background: rgba(255,255,255,0.7);
  }
  .contact-block {
    position: absolute;
    left: 292px; top: 50px;
  }
  .contact-name {
    font-weight: 700;
    font-size: 17px;
    letter-spacing: 1px;
    text-transform: uppercase;
    margin: 0;
  }
  .contact-role {
    font-weight: 500;
    font-size: 12px;
    letter-spacing: 0.5px;
    margin: 2px 0 10px;
  }
  .contact-list {
    list-style: none;
    margin: 0; padding: 0;
    font-family: "Arimo", sans-serif;
    font-size: 12px;
    line-height: 17px;
  }
  .contact-list li {
    display: flex;
    align-items: center;
    gap: 8px;
  }
  .contact-list svg { width: 9px; height: 9px; flex: none; }
  .address-band {
    position: absolute;
    left: 0; right: 0; bottom: 0;
    height: 58px;
    background: var(--paper);
  }
  .address-rule {
    position: absolute;
    left: 0; right: 0; top: 0;
    height: 3px;
    background: var(--brand-blue-deep);
    box-shadow: 0 4px 0 var(--paper), 0 5px 0 var(--brand-blue-deep);
  }
  .address-text {
    position: absolute;
    left: 0; right: 0; top: 22px;
    text-align: center;
    font-family: "Arimo", sans-serif;
    font-size: 13px;
    color: var(--brand-blue-deep);
  }
</style>
</head>
<body>
<div class="canvas">

  <section class="card card--front">
    <svg class="world-map" role="img" aria-label="Dotted world map in lighter blue behind the name" viewBox="0 0 500 250">
      <defs>
        <radialGradient id="mapTone" cx="50%" cy="45%" r="60%">
          <stop offset="0%" stop-color="#4f93d3" stop-opacity="0.55"/>
          <stop offset="100%" stop-color="#4f93d3" stop-opacity="0"/>
        </radialGradient>
      </defs>
      <rect width="500" height="250" fill="url(#mapTone)"/>
    </svg>
    <div class="front-wordmark">Veratus Global</div>
    <div class="front-tagline">Guiding Strategy | Building Lasting Results</div>
  </section>

  <section class="card card--back">
    <div class="back-wordmark">Veratus Global</div>
    <div class="back-divider"></div>
    <div class="contact-block">
      <p class="contact-name">Daniel Brooke</p>
      <p class="contact-role">Design Consultant</p>
      <ul class="contact-list">
        <li>
          <svg viewBox="0 0 10 10"><rect x="2.5" y="0.5" width="5" height="9" rx="1" fill="none" stroke="#fff" stroke-width="1"/></svg>
          555-014-2763
        </li>
        <li>
          <svg viewBox="0 0 10 10"><path d="M2 1 L4 1 L4.6 3 L3.4 4 Q4.5 6 6 6.6 L7 5.4 L9 6 L9 8 Q5 9 1 3 Z" fill="#fff"/></svg>
          01632 960418 (Northfield)
        </li>
        <li>
          <svg viewBox="0 0 10 10"><path d="M2 1 L4 1 L4.6 3 L3.4 4 Q4.5 6 6 6.6 L7 5.4 L9 6 L9 8 Q5 9 1 3 Z" fill="#fff"/></svg>
          01632 960752 (Ashcombe)
        </li>
        <li>
          <svg viewBox="0 0 10 10"><rect x="0.5" y="2" width="9" height="6" fill="none" stroke="#fff"/><path d="M0.5 2 L5 5.5 L9.5 2" fill="none" stroke="#fff"/></svg>
          hello@veratusglobal.com
        </li>
        <li>
          <svg viewBox="0 0 10 10"><circle cx="5" cy="5" r="4.3" fill="none" stroke="#fff"/><path d="M0.7 5 H9.3 M5 0.7 Q2 5 5 9.3 M5 0.7 Q8 5 5 9.3" fill="none" stroke="#fff" stroke-width="0.8"/></svg>
          www.veratusglobal.com
        </li>
      </ul>
    </div>
    <div class="address-band">
      <div class="address-rule"></div>
      <div class="address-text">Unit 8, The Meridian Court, Elm Park, Northfield, Hants NF4 2LP</div>
    </div>
  </section>

</div>
</body>
</html>
```